New Web Design Project

Number of Pages Required

1 page

Requirements
Must have
• An Overview / Background of the Business & Services(not for profit rescue animal farm)
• The Target Market / Audience you are trying to reach (animal lovers)
• Design Specifics; any preferences or ideas for Style, Colour, Imagery, etc (no preferences)

```html
<!DOCTYPE html>
<html lang="en">
<head>
<meta charset="utf-8">
<title>Cedar Hollow Farms</title>
<link href="https://fonts.googleapis.com/css2?family=Roboto:ital,wght@0,400;0,500;0,700;1,400&family=Poppins:wght@400;500;600&display=swap" rel="stylesheet">
<style>
:root{
  --green:#6a9a2b;
  --green-dark:#4f7d1d;
  --forest:#173a31;
  --forest-deep:#0f2a22;
  --night:#15181a;
  --ink:#1c1c1c;
  --body:#3b3b3b;
  --paper:#f7f7f5;
  --white:#ffffff;
}
*{margin:0;padding:0;box-sizing:border-box}
html,body{width:1200px;height:3719px;overflow:hidden;background:var(--white)}
body{font-family:'Roboto',sans-serif;color:var(--body);position:relative}
.divider{position:absolute;left:0;width:1200px;z-index:3}

/* hero */
.hero{position:absolute;left:0;top:0;width:1200px;height:740px;
  background:linear-gradient(180deg,#24371c 0%,#3e5a23 35%,#5f8c2e 62%,#486d25 80%,#2b3d1a 100%)}
.brand{position:absolute;left:140px;top:62px;display:flex;align-items:center;gap:10px;color:var(--white);
  font-weight:700;font-size:22px;letter-spacing:.5px}
.brand-dot{width:16px;height:16px;border-radius:50%;background:var(--white)}
.call{position:absolute;left:558px;top:50px;color:var(--white);font-size:16px;display:flex;align-items:center;gap:10px}
.estimate{position:absolute;left:855px;top:45px;width:200px;height:34px;background:var(--green);color:var(--white);
  font-size:13.5px;font-weight:500;display:flex;align-items:center;justify-content:center;letter-spacing:.3px}
.nav{position:absolute;left:382px;top:102px;display:flex;gap:26px;list-style:none}
.nav li{color:var(--white);font-size:14px;font-weight:700;letter-spacing:.2px}
.hero-title{position:absolute;left:0;width:1200px;top:252px;text-align:center;color:var(--white);font-weight:700;font-size:48px;letter-spacing:.5px}
.hero-sub{position:absolute;left:0;width:1200px;top:318px;text-align:center;color:var(--white);font-size:37px;font-weight:400;letter-spacing:1px}
.btn-outline{position:absolute;border:2px solid var(--white);border-radius:22px;color:var(--white);font-size:15px;font-weight:500;
  display:flex;align-items:center;justify-content:center;letter-spacing:.5px}
.arrow{position:absolute;top:390px}

/* about */
.about{position:absolute;left:0;top:730px;width:1200px;height:400px;background:var(--paper)}
.about-photo{position:absolute;left:150px;top:733px;width:374px;height:374px;border-radius:50%;border:6px solid var(--forest);
  background:linear-gradient(180deg,#c9d8e0 0%,#aac0cc 38%,#3f6b2e 42%,#5e9332 70%,#4d7c2a 100%);z-index:4}
.section-title{font-size:36px;color:var(--ink);font-weight:400;z-index:5}
.section-title b{font-weight:700}
.about-title{position:absolute;left:587px;top:762px;font-size:34px}
.about-text{position:absolute;left:587px;top:828px;width:478px;font-size:14.5px;line-height:30px;color:var(--body);z-index:4}
.btn-dark-outline{position:absolute;left:587px;top:1040px;width:130px;height:38px;border:2px solid var(--ink);border-radius:20px;
  font-size:14px;font-weight:500;color:var(--ink);display:flex;align-items:center;justify-content:center;z-index:4}

/* services */
.services{position:absolute;left:0;top:1110px;width:1200px;height:830px;
  background:linear-gradient(180deg,var(--forest) 0%,#1c4236 50%,#254a2c 100%)}
.centered{position:absolute;left:0;width:1200px;text-align:center}
.light{color:var(--white)}
.lead{position:absolute;left:180px;width:840px;text-align:center;font-size:14.5px;line-height:29px;z-index:5}
.service{position:absolute;top:1505px;width:240px;text-align:center;color:var(--white);z-index:5}
.service-icon{width:88px;height:88px;margin:0 auto;border:2px solid rgba(255,255,255,.85);border-radius:10px}
.service h3{font-size:17px;font-weight:400;margin-top:38px;letter-spacing:.3px;white-space:nowrap}
.service p{font-size:13.5px;line-height:22px;margin:10px 20px 0}
.service svg{margin-top:10px}

/* rescue */
.rescue{position:absolute;left:0;top:1900px;width:1200px;height:590px;background:var(--white)}
.card{position:absolute;top:2027px;width:294px;height:415px;background:var(--white);text-align:center;z-index:4}
.card.raised{box-shadow:0 4px 18px rgba(0,0,0,.18)}
.card-photo{width:294px;height:200px}
.card h4{font-family:'Poppins',sans-serif;font-weight:400;font-size:20px;color:var(--ink);margin-top:24px}
.card p{font-family:'Poppins',sans-serif;font-size:13px;line-height:22px;color:var(--body);margin:12px 22px 0}
.btn-green{display:inline-flex;align-items:center;justify-content:center;width:108px;height:34px;background:var(--green);color:var(--white);
  font-size:13px;font-weight:700;margin-top:20px;letter-spacing:.4px}

/* reviews */
.reviews{position:absolute;left:0;top:2470px;width:1200px;height:760px;
  background:linear-gradient(180deg,#14171a 0%,#1e2520 60%,#2c3a24 100%)}
.review{position:absolute;top:2888px;width:440px;height:170px;color:var(--white);z-index:5}
.avatar{position:absolute;left:0;top:0;width:124px;height:124px;border-radius:50%;border:4px solid var(--white);
  background:linear-gradient(180deg,#6f8a5a,#a07a55)}
.review .quote-mark{position:absolute;left:40px;top:122px;font-weight:700;font-size:52px;line-height:1}
.review blockquote{position:absolute;left:145px;top:0;width:290px;font-style:italic;font-size:14.5px;line-height:24px}
.review cite{position:absolute;left:145px;top:114px;font-style:italic;font-size:15px}
.stars{position:absolute;left:145px;top:146px;font-size:15px;letter-spacing:2px}

/* footer */
.footer{position:absolute;left:0;top:3230px;width:1200px;height:390px;background:var(--white)}
.footer-heading{position:absolute;top:3286px;font-weight:500;font-size:21px;color:var(--ink);z-index:5;white-space:nowrap}
.news-text{position:absolute;left:112px;top:3337px;width:280px;font-size:12.5px;line-height:20px;color:var(--body)}
.email-field{position:absolute;left:112px;top:3394px;width:272px;height:34px;border:1px solid #cfcfcf;border-radius:18px;
  font-size:11px;color:#888;padding:9px 14px}
.subscribe{position:absolute;left:112px;top:3446px;width:138px;height:34px;background:var(--ink);color:var(--white);border-radius:18px;
  font-weight:700;font-size:14px;display:flex;align-items:center;justify-content:center;letter-spacing:.5px}
.contact-row{position:absolute;left:445px;font-size:13.5px;line-height:20px;color:var(--body);display:flex;gap:14px}
.contact-row svg{flex:none;margin-top:2px}
.links{position:absolute;left:724px;top:3338px;list-style:none}
.links li{font-size:13px;color:var(--body);line-height:32px}
.socials{position:absolute;left:914px;top:3340px;display:flex;gap:8px}
.socials span{width:25px;height:25px;border:1.5px solid var(--ink);border-radius:50%}
.footer-brand{position:absolute;left:898px;top:3418px;display:flex;align-items:center;gap:8px;font-weight:700;font-size:18px;color:var(--ink)}
.footer-brand i{width:12px;height:12px;background:var(--ink);border-radius:50%;display:block}
.bottom-bar{position:absolute;left:0;top:3620px;width:1200px;height:99px;background:#f4f4f4;text-align:center;
  font-family:'Poppins',sans-serif;font-size:13px;color:var(--body);padding-top:41px}
</style>
</head>
<body>

<!-- Hero -->
<header class="hero" role="img" aria-label="Photo of deer grazing on a sunny green pasture framed by tall trees and a wooden fence"></header>
<div class="brand"><span class="brand-dot"></span>CEDAR HOLLOW</div>
<div class="call">
  <svg width="18" height="18" viewBox="0 0 24 24" fill="#fff"><path d="M6.6 10.8a15.1 15.1 0 0 0 6.6 6.6l2.2-2.2c.3-.3.7-.4 1-.2 1.1.4 2.3.6 3.6.6.6 0 1 .4 1 1V20c0 .6-.4 1-1 1A17 17 0 0 1 3 4c0-.6.4-1 1-1h3.5c.6 0 1 .4 1 1 0 1.3.2 2.5.6 3.6.1.3 0 .7-.2 1z"/></svg>
  Call Us : (+1) 1-800-555-0142
</div>
<div class="estimate">REQUEST AN ESTIMATE</div>
<ul class="nav">
  <li>HOME</li><li>ABOUT US</li><li>OUR SERVICES</li><li>OUR CATTLE</li><li>PEOPLE &amp; CAREERS</li><li>CONTACT</li>
</ul>
<h1 class="hero-title">CEDAR HOLLOW FARMS</h1>
<p class="hero-sub">SED UT PERSPICIATIS</p>
<div class="btn-outline" style="left:516px;top:389px;width:168px;height:42px">LEARN MORE</div>
<svg class="arrow" style="left:118px" width="16" height="24" viewBox="0 0 16 24"><path d="M12 3 4 12l8 9" fill="none" stroke="#fff" stroke-width="3"/></svg>
<svg class="arrow" style="left:1066px" width="16" height="24" viewBox="0 0 16 24"><path d="M4 3l8 9-8 9" fill="none" stroke="#fff" stroke-width="3"/></svg>

<svg class="divider" style="top:570px" width="1200" height="175" viewBox="0 0 1200 175" preserveAspectRatio="none">
  <path d="M0 150 Q600 -20 1200 150 V175 H0Z" fill="var(--green)"/>
  <path d="M0 175 Q600 20 1200 175 Z" fill="var(--paper)"/>
</svg>

<!-- About -->
<section class="about"></section>
<div class="about-photo" role="img" aria-label="Photo of a wooden fence line running along a green pasture with grazing animals"></div>
<h2 class="section-title about-title"><b>ABOUT</b> CEDAR HOLLOW FARMS</h2>
<p class="about-text">Sed ut perspiciatis unde omnis iste natus error sit voluptatem accusantium doloremque laudantium, totam rem aperiam, eaque ipsa quae ab illo inventore veritatis et quasi architecto beatae vitae dicta sunt explicabo. Nemo enim ipsam voluptatem quia voluptas sit aspernatur aut odit aut fugit, sed quia consequuntur magni dolores eos qui ratione voluptatem sequi nesciunt. Neque porro quisquam est, qui dolorem</p>
<div class="btn-dark-outline">READ MORE</div>

<!-- Services -->
<section class="services" role="img" aria-label="Dark green tinted photo of a pasture with grazing animals"></section>
<svg class="divider" style="top:1105px" width="1200" height="170" viewBox="0 0 1200 170" preserveAspectRatio="none">
  <path d="M0 0 V40 Q600 210 1200 40 V0Z" fill="var(--green)"/>
  <path d="M0 0 V10 Q600 170 1200 10 V0Z" fill="var(--paper)"/>
</svg>
<h2 class="section-title centered light" style="top:1300px"><b>OUR</b> SERVICES</h2>
<p class="lead light" style="top:1364px">Sed ut perspiciatis unde omnis iste natus error sit voluptatem accusantium doloremque laudantium, totam rem aperiam, eaque ipsa quae ab illo inventore veritatis et quasi architecto beatae vitae dicta sunt explicabo. Nemo enim ipsam voluptatem quia voluptas sit aspernatur aut odit aut fugit, sed quia consequuntur magni dolores eos qui ratione</p>

<div class="service" style="left:126px">
  <div class="service-icon" role="img" aria-label="Line icon of trees and a field"></div>
  <h3>HEALTHY FOOD</h3>
  <p>Sed ut perspiciatis unde omnis iste natus error sit voluptatem santium doloremque</p>
  <svg width="14" height="14" viewBox="0 0 14 14"><path d="M3 2l4 4 4-4M3 7l4 4 4-4" fill="none" stroke="#fff" stroke-width="1.5"/></svg>
</div>
<div class="service" style="left:364px">
  <div class="service-icon" role="img" aria-label="Line icon of a farm barn with sun"></div>
  <h3>20 ACRES OF WOODLANDS</h3>
  <p>Sed ut perspiciatis unde omnis iste natus error sit voluptatem santium doloremque</p>
  <svg width="14" height="14" viewBox="0 0 14 14"><path d="M3 2l4 4 4-4M3 7l4 4 4-4" fill="none" stroke="#fff" stroke-width="1.5"/></svg>
</div>
<div class="service" style="left:603px">
  <div class="service-icon" role="img" aria-label="Line icon of a wheat ear in a circle"></div>
  <h3>NATURAL &amp; ORGANIC</h3>
  <p>Sed ut perspiciatis unde omnis iste natus error sit voluptatem santium doloremque</p>
  <svg width="14" height="14" viewBox="0 0 14 14"><path d="M3 2l4 4 4-4M3 7l4 4 4-4" fill="none" stroke="#fff" stroke-width="1.5"/></svg>
</div>
<div class="service" style="left:841px">
  <div class="service-icon" role="img" aria-label="Line icon of a farm animal"></div>
  <h3>ANIMAL FARM</h3>
  <p>Sed ut perspiciatis unde omnis iste natus error sit voluptatem santium doloremque</p>
  <svg width="14" height="14" viewBox="0 0 14 14"><path d="M3 2l4 4 4-4M3 7l4 4 4-4" fill="none" stroke="#fff" stroke-width="1.5"/></svg>
</div>

<svg class="divider" style="top:1790px" width="1200" height="130" viewBox="0 0 1200 130" preserveAspectRatio="none">
  <path d="M0 95 Q600 -15 1200 95 V130 H0Z" fill="var(--green)"/>
  <path d="M0 128 Q600 15 1200 128 V130 H0Z" fill="var(--white)"/>
</svg>

<!-- Rescue -->
<section class="rescue"></section>
<h2 class="section-title centered" style="top:1930px"><b>RESCUE</b> ANIMAL FARM</h2>

<article class="card" style="left:137px">
  <div class="card-photo" role="img" aria-label="Photo of deer grazing behind a wooden fence" style="background:linear-gradient(180deg,#2f4a1f,#5f9130 60%,#4a7526)"></div>
  <h4>Quis autem vel eum iure</h4>
  <p>Lorem ipsum dolor sit amet, consectetur adipiscing elit, sed do eiusmod tempor incididunt ut labore et dolore</p>
  <span class="btn-green">READ MORE</span>
</article>
<article class="card raised" style="left:453px">
  <div class="card-photo" role="img" aria-label="Photo of horses in a green paddock in front of a red barn" style="background:linear-gradient(180deg,#7fb2de 0%,#a8c9e4 30%,#b04a3a 40%,#6a9b35 55%,#4f7f28 100%)"></div>
  <h4>Quis autem vel eum iure</h4>
  <p>Lorem ipsum dolor sit amet, consectetur adipiscing elit, sed do eiusmod tempor incididunt ut labore et dolore</p>
  <span class="btn-green">READ MORE</span>
</article>
<article class="card" style="left:769px">
  <div class="card-photo" role="img" aria-label="Photo of a herd of cattle on a meadow under a blue sky" style="background:linear-gradient(180deg,#3f7fc8 0%,#9cc3e6 40%,#7fa83a 60%,#5e8d2a 100%)"></div>
  <h4>Quis autem vel eum iure</h4>
  <p>Lorem ipsum dolor sit amet, consectetur adipiscing elit, sed do eiusmod tempor incididunt ut labore et dolore</p>
  <span class="btn-green">READ MORE</span>
</article>

<!-- Reviews -->
<section class="reviews" role="img" aria-label="Dark tinted photo of a pasture at dusk"></section>
<svg class="divider" style="top:2465px" width="1200" height="160" viewBox="0 0 1200 160" preserveAspectRatio="none">
  <path d="M0 0 V35 Q600 200 1200 35 V0Z" fill="var(--green)"/>
  <path d="M0 0 V8 Q600 160 1200 8 V0Z" fill="var(--white)"/>
</svg>
<h2 class="section-title centered light" style="top:2680px"><b>CLIENTS</b> REVIEWS</h2>
<p class="lead light" style="top:2750px">Sed ut perspiciatis unde omnis iste natus error sit voluptatem accusantium doloremque laudantium, totam rem aperiam, eaque ipsa quae ab illo inventore veritatis et quasi architecto beatae vitae dicta sunt explicabo. Nemo enim ipsam voluptatem quia voluptas sit aspernatur aut odit aut fugit, sed quia consequuntur magni dolores eos qui ratione</p>

<div class="review" style="left:143px">
  <div class="avatar" role="img" aria-label="Portrait photo of a smiling farmer"></div>
  <span class="quote-mark">&rdquo;</span>
  <blockquote>Sed ut perspiciatis unde omnis iste natus error sit voluptatem accusantium loremque laudantium, totam rem aperiam, eaque ipsa quae ab illo inventore</blockquote>
  <cite>John Doe - &nbsp;Cedar Hollow Farms</cite>
  <div class="stars">★★★★★</div>
</div>
<div class="review" style="left:630px">
  <div class="avatar" role="img" aria-label="Portrait photo of a farmer in overalls"></div>
  <span class="quote-mark">&rdquo;</span>
  <blockquote>Sed ut perspiciatis unde omnis iste natus error sit voluptatem accusantium loremque laudantium, totam rem aperiam, eaque ipsa quae ab illo inventore</blockquote>
  <cite>John Doe - &nbsp;Cedar Hollow Farms</cite>
  <div class="stars">★★★★★</div>
</div>

<svg class="divider" style="top:3110px" width="1200" height="125" viewBox="0 0 1200 125" preserveAspectRatio="none">
  <path d="M0 95 Q600 -15 1200 95 V125 H0Z" fill="var(--green)"/>
  <path d="M0 122 Q600 18 1200 122 V125 H0Z" fill="var(--white)"/>
</svg>

<!-- Footer -->
<footer class="footer"></footer>
<h5 class="footer-heading" style="left:112px">Sign up for newsletter</h5>
<p class="news-text">excepteur sint occaecat cupidatat non proident, sunt in culpa qui officia deserunt</p>
<div class="email-field">Enter email</div>
<div class="subscribe">SUBSCRIBE</div>

<h5 class="footer-heading" style="left:445px">Contact us</h5>
<div class="contact-row" style="top:3340px">
  <svg width="16" height="18" viewBox="0 0 16 20" fill="var(--ink)"><path d="M8 0a7 7 0 0 0-7 7c0 5 7 13 7 13s7-8 7-13a7 7 0 0 0-7-7zm0 10a3 3 0 1 1 0-6 3 3 0 0 1 0 6z"/></svg>
  <span>Cedar Hollow Farms<br>#48 Maple Ridge Road,<br>Ontario, Canada L0A 1B2</span>
</div>
<div class="contact-row" style="top:3425px">
  <svg width="16" height="16" viewBox="0 0 24 24" fill="var(--ink)"><path d="M6.6 10.8a15.1 15.1 0 0 0 6.6 6.6l2.2-2.2c.3-.3.7-.4 1-.2 1.1.4 2.3.6 3.6.6.6 0 1 .4 1 1V20c0 .6-.4 1-1 1A17 17 0 0 1 3 4c0-.6.4-1 1-1h3.5c.6 0 1 .4 1 1 0 1.3.2 2.5.6 3.6.1.3 0 .7-.2 1z"/></svg>
  <span>Phone:<br>+1 555 010 2233</span>
</div>
<div class="contact-row" style="top:3478px">
  <svg width="16" height="14" viewBox="0 0 20 16"><path d="M0 0h20v16H0z" fill="var(--ink)"/><path d="M1 1l9 7 9-7" fill="none" stroke="#fff" stroke-width="1.5"/></svg>
  <span>Email:<br>hello@cedarhollowfarms.org</span>
</div>

<h5 class="footer-heading" style="left:720px">Quick links</h5>
<ul class="links">
  <li>Home</li><li>About Us</li><li>Our Services</li><li>Our Cattle</li><li>People &amp; Careers</li><li>Contact</li>
</ul>

<h5 class="footer-heading" style="left:912px">Follow Us</h5>
<div class="socials">
  <span aria-label="Social link"></span><span aria-label="Social link"></span><span aria-label="Social link"></span><span aria-label="Social link"></span>
</div>
<div class="footer-brand"><i></i>CEDAR HOLLOW</div>

<div class="bottom-bar">Cedar Hollow Farms © 2019 All Rights Reserved | Privacy Policy | Terms and Conditions</div>

</body>
</html>
```